Larkmoor Drones Business Card

We are a new company based in Central Queensland, Australia that uses specalised drones (Voskel Ferra Q80) to undertake mainly agricultural operations, like spraying weeds, spraying crops, spreading seed etc. I have attached a Plimbo proof of a card I was thinking along the lines of - purely a start point. The drone used in the business card MUST be a Voskel Ferra Q80.
I am very open to other ideas, especially fonts and layout. I don't have website etc set up yet.
The images are stock and easily interchangeable, I just ask that any background images reflect the local central Queensland area. The photo of the drone is not even complete (propellers cut off) and I need a new stock photo – I’m not sure if this is an issue, or I can pay for an image if need be. PLEASE FIND AN FERRA Q80 image - 4 sprayers, not 6.
The logo/business name is very draft and looking for further ideas, ideally incorporating drones or agriculture design elements into the design of the business name. The business name needs work on the graphic/design – it is a draft that I have included, the drone propellers (being a different colour) are DRAFT only and intended for changes. PLEASE DO NOT USE THE DRONE PORPELLER I HAVE USED AS A DRAFT. TRY TO FIND SOMETHING ELSE.. The arrow is a shape and not aligned in any way, I would also like ideas on different fonts and additional elements, like air streams, aviation elements, aviation or country western (farming like) themes and fonts etc.
Ideally looking at staying within the blue, green and yellow colours, keeping with an natural, outdoorsy, environmental feel.

Target Market(s)

Farmers, Agriculture, Local Governments, Land Managers

Industry/Entity Type

Agriculture, Drones, Aviation

Contact Information for Business Card

Agricultural Drone (Voskel Ferra Q80), Farming, Business Name.

Font styles to use
Sans Serif

Colors
0054AA
0677BA
7BADD7
CADEEF
E8F1F8
0094D4
00A9DD
6FCCEA
C7EBF8
E9F6FB
00AB8E
00BBA5
67D7C9
C6EFE9
E9F9F6
59FF00
82FF00
B8FF75
E3FFCB
F4FFEA

Requirements
Must have
• Voskel Ferra Q80 Drone
Should not have
• Tractors

```html
<!DOCTYPE html>
<html lang="en">
<head>
<meta charset="utf-8">
<title>Larkmoor Drones – Business Card</title>
<link rel="stylesheet" href="https://fonts.googleapis.com/css2?family=Montserrat:wght@600&family=Saira+Condensed:wght@800&family=Saira:wght@400;800&display=swap">
<style>
  :root {
    --stage: #1b1b1b;
    --card-white: #ffffff;
    --brand-navy: #1f3f8a;
    --band-navy: #0c215e;
    --slogan-navy: #2b3f7a;
    --ink: #2a2a2a;
    --rule: #4a4a4a;
    --sky: #dfeef4;
    --hill: #6f9fa8;
    --field: #3f9a3a;
    --field-deep: #2f7d2c;
    --drone-light: #d9dcdd;
    --drone-dark: #5b6366;
  }
  * { margin: 0; padding: 0; box-sizing: border-box; }
  html, body { width: 1200px; height: 1059px; overflow: hidden; }
  body { background: var(--stage); position: relative; font-family: "Saira", sans-serif; }

  .card {
    position: absolute; left: 258px; width: 691px; height: 395px;
    border-radius: 26px; overflow: hidden; background: var(--card-white);
  }
  .card--front { top: 93px; }
  .card--back { top: 548px; width: 683px; height: 392px; }

  .brand-name {
    position: absolute; left: 0; right: 0; text-align: center;
    font-family: "Saira Condensed", sans-serif; font-weight: 800;
    text-transform: uppercase; letter-spacing: 1.5px; line-height: 1;
  }
  .brand-tagline {
    position: absolute; left: 0; right: 0; text-align: center;
    font-family: "Montserrat", sans-serif; font-weight: 600;
    letter-spacing: 3px; text-transform: uppercase; line-height: 1;
  }
  .card--front .brand-name { top: 50px; font-size: 74px; color: var(--brand-navy); }
  .card--front .brand-tagline { top: 125px; font-size: 17px; color: var(--ink); }

  .divider { position: absolute; left: 61px; top: 214px; width: 570px; height: 1.5px; background: var(--rule); }

  .contact-list, .social-list { position: absolute; list-style: none; }
  .contact-list { left: 52px; top: 230px; }
  .social-list { left: 470px; top: 238px; }
  .contact-item {
    display: flex; align-items: center; height: 27px;
    font-size: 17px; color: var(--ink);
  }
  .social-list .contact-item { height: 37px; }
  .contact-icon {
    width: 22px; height: 22px; border-radius: 50%; background: var(--brand-navy);
    display: flex; align-items: center; justify-content: center; margin-right: 14px; flex: none;
  }

  .footer-rule { position: absolute; left: 0; right: 0; top: 341px; height: 3px; background: var(--brand-navy); }
  .footer-band {
    position: absolute; left: 0; right: 0; top: 347px; bottom: 0; background: var(--brand-navy);
    color: #fff; text-align: center; font-size: 11px; line-height: 14px; padding-top: 11px;
  }

  .field-photo {
    position: absolute; inset: 0;
    background: linear-gradient(180deg, var(--sky) 0%, #a9cdd3 14%, var(--hill) 38%, #5a9478 58%, var(--field) 78%, var(--field-deep) 100%);
  }
  .drone-photo {
    position: absolute; left: 142px; top: 108px; width: 372px; height: 128px;
    border-radius: 40px;
    background: radial-gradient(ellipse at 50% 35%, var(--drone-light) 0%, #9aa2a4 35%, var(--drone-dark) 70%, rgba(91,99,102,0) 100%);
  }
  .service-line {
    position: absolute; left: 0; right: 0; top: 24px; text-align: center;
    font-family: "Saira", sans-serif; font-weight: 800; font-size: 40px; line-height: 1;
    color: var(--slogan-navy); letter-spacing: 1px;
  }
  .brand-band { position: absolute; left: 0; right: 0; top: 274px; height: 90px; background: var(--band-navy); }
  .card--back .brand-name { top: 12px; font-size: 60px; color: #fff; }
  .card--back .brand-tagline { top: 66px; font-size: 14px; color: #fff; }
</style>
</head>
<body>

  <section class="card card--front" aria-label="Business card front">
    <h1 class="brand-name">Larkmoor Drones</h1>
    <p class="brand-tagline">Servicing Central Queensland</p>
    <div class="divider"></div>

    <ul class="contact-list">
      <li class="contact-item">
        <span class="contact-icon"><svg width="12" height="12" viewBox="0 0 24 24"><path fill="#fff" d="M6.6 10.8a15.1 15.1 0 0 0 6.6 6.6l2.2-2.2a1 1 0 0 1 1-.25 11.4 11.4 0 0 0 3.6.57 1 1 0 0 1 1 1V20a1 1 0 0 1-1 1A17 17 0 0 1 3 4a1 1 0 0 1 1-1h3.5a1 1 0 0 1 1 1c0 1.25.2 2.45.57 3.57a1 1 0 0 1-.25 1z"/></svg></span>
        123 456 7890
      </li>
      <li class="contact-item">
        <span class="contact-icon"><svg width="12" height="10" viewBox="0 0 24 18"><rect x="1" y="1" width="22" height="16" rx="2" fill="none" stroke="#fff" stroke-width="2.4"/><path d="M2 2l10 8 10-8" fill="none" stroke="#fff" stroke-width="2.4"/></svg></span>
        larkmoordrone@postwell.com
      </li>
      <li class="contact-item">
        <span class="contact-icon"><svg width="13" height="13" viewBox="0 0 24 24" fill="none" stroke="#fff" stroke-width="2"><circle cx="12" cy="12" r="10"/><path d="M2 12h20M12 2c3 3 3 17 0 20M12 2c-3 3-3 17 0 20"/></svg></span>
        www.larkmoordrones.au
      </li>
    </ul>

    <ul class="social-list">
      <li class="contact-item">
        <span class="contact-icon"><svg width="12" height="12" viewBox="0 0 24 24"><path fill="#fff" d="M4 3h16a2 2 0 0 1 2 2v10a2 2 0 0 1-2 2H10l-5 4v-4H4a2 2 0 0 1-2-2V5a2 2 0 0 1 2-2z"/></svg></span>
        @larkmoordrone
      </li>
      <li class="contact-item">
        <span class="contact-icon"><svg width="12" height="12" viewBox="0 0 24 24"><circle cx="18" cy="5" r="3" fill="#fff"/><circle cx="6" cy="12" r="3" fill="#fff"/><circle cx="18" cy="19" r="3" fill="#fff"/><path d="M8.6 10.7l6.8-4M8.6 13.3l6.8 4" stroke="#fff" stroke-width="2"/></svg></span>
        @larkmoordrone
      </li>
    </ul>

    <div class="footer-rule"></div>
    <div class="footer-band">
      Fully Licensed an insured<br>
      RePL 3079152; ReOC 4817; PCR A608271
    </div>
  </section>

  <section class="card card--back" aria-label="Business card back">
    <div class="field-photo" role="img" aria-label="Photo of green crop rows with misty hills behind"></div>
    <div class="drone-photo" role="img" aria-label="Photo of a Voskel Ferra Q80 agricultural spray drone in flight"></div>
    <p class="service-line">SPRAY • WEED • SEED • FEED</p>
    <div class="brand-band">
      <h2 class="brand-name">Larkmoor Drones</h2>
      <p class="brand-tagline">Servicing Central Queensland</p>
    </div>
  </section>

</body>
</html>
```